Inspirational Quotes Poster Set

Brookloft is a stylish coworking space, which has a design-oriented vintage look from the 60's with an industrial touch (www.brookloft-example.com) Brookloft Quote Poster Set of 16 posters. The poster should be typo oriented and rather simple. Reflecting a bit the clean billboard design from the sixties. Minimal / simple graphical elements

Target Market(s)

Startups and Entrepreneurs

Industry/Entity Type

Startup

Font styles to use
Sans Serif

Colors

Designer to choose colors to be used in the design.

Requirements
Must have
• Posters need to be on and very stylish

```html
<!DOCTYPE html>
<html lang="en">
<head>
<meta charset="utf-8">
<title>Brookloft Quote Poster Set – Risk Taker</title>
<link rel="stylesheet" href="https://fonts.googleapis.com/css2?family=Josefin+Sans:wght@600&family=Carlito:wght@400&display=swap">
<style>
  :root {
    --poster-rose: #d07f7c;
    --poster-ink: #ffffff;
  }
  html, body {
    margin: 0;
    padding: 0;
    width: 1200px;
    height: 675px;
    overflow: hidden;
    background: var(--poster-rose);
  }
  .poster {
    display: block;
    width: 1200px;
    height: 675px;
    background: var(--poster-rose);
  }
  .rule { fill: var(--poster-ink); }
  .quote-line {
    font-family: "Josefin Sans", sans-serif;
    font-weight: 600;
    font-size: 62px;
    fill: var(--poster-ink);
    word-spacing: 4px;
  }
  .quote-initial { font-size: 80px; }
  .attribution {
    font-family: "Carlito", "Calibri", sans-serif;
    font-size: 52px;
    fill: var(--poster-ink);
    letter-spacing: 1px;
  }
</style>
</head>
<body>
  <svg class="poster" viewBox="0 0 1200 675" xmlns="http://www.w3.org/2000/svg" role="img" aria-label="Quote poster: If you're not a risk taker you should get the hell out of business. Hal Brenner, Burgerline Founder">
    <rect class="rule rule-top" x="147" y="104" width="908" height="7"/>

    <text class="quote-line" x="611" y="224" text-anchor="middle"><tspan class="quote-initial">I</tspan>F YOU’RE NOT A RISK TAKER</text>
    <text class="quote-line" x="611" y="342" text-anchor="middle"><tspan class="quote-initial">Y</tspan>OU SHOULD GET THE HELL</text>
    <text class="quote-line" x="621" y="464" text-anchor="middle">OUT OF BUSINESS.</text>

    <rect class="rule rule-bottom" x="138" y="512" width="908" height="7"/>

    <text class="attribution" x="620" y="607" text-anchor="middle">Hal Brenner, Burgerline Founder</text>
  </svg>
</body>
</html>
```